The Vellmark Company Sweet Packaging Design

The Vellmark Goods Company is looking for a logo and label design for an upcoming line of honey based health and beauty products that are sourced from the Polynesian Islands (Hawaii, New Zealand, Fiji etc.).The brand will be premium price positioned and the design and packaging should exude class and quality.The design should be flexible enough to add products from future locations.We would like to see the design across three different product forms:1. Glass Honey Jar (main product)2. Hand cream / lotion (pump bottle, or lotion tube)3. Small box (e.g. throat lozenges / gum packet etc.)The Polynesia Islands are unique and exotic locations; the design/packaging should reflect this but should not be overly complicated. Each individual island has their own distinct culture and history but they have many commonalities which fall under "Polynesian Culture". The Vellmark Goods Company is an umbrella brand that should be able to support a growing number of products.Possible designs may (but are not required to) incorporate local flowers (Hawaii / Hibiscus flower, New Zealand / Manuka Flower etc.) into the design, Islands, and boutique feel (elegant classy looking)Please feel free to ask more questions for further guidance but we really want to see where the creative process can take us outside of what we have already considered internally.
Updates

We needed to modify our idea slightly because of competition.

We needed extend to get a few more ideas. We did not want to copy our competition and needed to add a part to our design that we did not include before.

Target Market(s)

Health conscious people. Honey lovers.

Font styles to use
Serif
Sans Serif
Decorative

Colors

Designer to choose colors to be used in the design.

Requirements
Must have
• a little tribal look. because its 100% polynesian Honey.. it would be nice to have the fee of that in the design..

```html
<!DOCTYPE html>
<html lang="en">
<head>
<meta charset="utf-8">
<title>Hibiscus Honey Throat Lozenges – Box Front</title>
<link rel="stylesheet" href="https://fonts.googleapis.com/css2?family=Karla:wght@400&family=DM+Serif+Display&family=Libre+Caslon+Text:wght@700&display=swap">
<style>
  :root {
    --page-bg: #e3e4ea;
    --box-bg: #2c2c2d;
    --box-edge: #232324;
    --flower-tone: #3e3e40;
    --flower-tone-soft: rgba(62, 62, 64, 0);
    --ink-light: #f1f1f1;
  }
  * { margin: 0; padding: 0; box-sizing: border-box; }
  html, body {
    width: 1200px;
    height: 890px;
    overflow: hidden;
    background: var(--page-bg);
  }
  .canvas {
    position: relative;
    width: 1200px;
    height: 890px;
  }
  .box-front {
    position: absolute;
    left: 100px;
    top: 150px;
    width: 1000px;
    height: 590px;
    background: var(--box-bg);
    border-top: 6px solid var(--box-edge);
    overflow: hidden;
    color: var(--ink-light);
    text-align: center;
  }
  .flower-art {
    position: absolute;
    width: 274px;
    height: 242px;
  }
  .flower-art--top-left { left: 0; top: 6px; }
  .flower-art--top-right { left: 716px; top: 6px; }
  .flower-art--bottom-left { left: 0; top: 320px; }
  .flower-art--bottom-right { left: 716px; top: 320px; }

  .brand-mark {
    position: absolute;
    left: 0;
    right: 0;
    top: 40px;
    display: flex;
    flex-direction: column;
    align-items: center;
  }
  .brand-mark__circle {
    width: 150px;
    height: 150px;
    border: 2px solid var(--ink-light);
    border-radius: 50%;
  }
  .brand-mark__name {
    margin-top: 16px;
    font-family: "Libre Caslon Text", serif;
    font-weight: 700;
    font-size: 11px;
    letter-spacing: 0.2px;
  }
  .product-flavour,
  .product-claim {
    position: absolute;
    left: 0;
    right: 0;
    font-family: "Karla", sans-serif;
    font-weight: 400;
    font-size: 29px;
    letter-spacing: 1px;
  }
  .product-flavour { top: 280px; }
  .product-claim { top: 397px; }
  .product-name {
    position: absolute;
    left: 0;
    right: 0;
    top: 318px;
    font-family: "DM Serif Display", serif;
    font-weight: 400;
    font-size: 54px;
    letter-spacing: 1px;
  }
  .product-count {
    position: absolute;
    left: 0;
    right: 0;
    top: 527px;
    font-family: "Libre Caslon Text", serif;
    font-weight: 700;
    font-size: 26px;
  }
</style>
</head>
<body>
<div class="canvas">
  <section class="box-front">
    <svg class="flower-art flower-art--top-left" viewBox="0 0 274 242" role="img" aria-label="Hibiscus flower with leaves illustration">
      <defs>
        <radialGradient id="flowerGlow">
          <stop offset="0" stop-color="#454547"/>
          <stop offset="0.7" stop-color="#3a3a3c"/>
          <stop offset="1" stop-color="#2c2c2d"/>
        </radialGradient>
      </defs>
      <ellipse cx="137" cy="121" rx="137" ry="121" fill="url(#flowerGlow)"/>
    </svg>
    <svg class="flower-art flower-art--top-right" viewBox="0 0 274 242" role="img" aria-label="Hibiscus flower with leaves illustration">
      <ellipse cx="137" cy="121" rx="137" ry="121" fill="url(#flowerGlow)"/>
    </svg>
    <svg class="flower-art flower-art--bottom-left" viewBox="0 0 274 242" role="img" aria-label="Hibiscus flower with leaves illustration">
      <ellipse cx="137" cy="121" rx="137" ry="121" fill="url(#flowerGlow)"/>
    </svg>
    <svg class="flower-art flower-art--bottom-right" viewBox="0 0 274 242" role="img" aria-label="Hibiscus flower with leaves illustration">
      <ellipse cx="137" cy="121" rx="137" ry="121" fill="url(#flowerGlow)"/>
    </svg>

    <div class="brand-mark">
      <div class="brand-mark__circle"></div>
      <p class="brand-mark__name">The Vellmark Goods Company</p>
    </div>

    <p class="product-flavour">Hibiscus Honey</p>
    <h1 class="product-name">Throat Lozenges</h1>
    <p class="product-claim">Antibacterial</p>
    <p class="product-count">16 Lozenges</p>
  </section>
</div>
</body>
</html>
```